Heron Home Inspections website

I need a website for a new company called Heron Home Inspections, LLC. based in Northern Virginia. I'd like the site built on the url heroninspections.example and incorporating the graphics that I attached.
Updates

Project Deadline Extended
Reason: I got bogged down with my job, with a daughter moving, and with two daughters who are in their final stages of pregnancy. I started this web design job at a really bad time in my life. I do appreciate all of the hard work that the designers have put forth and I will soon make my selection. Thank you, Tom

Target Market(s)

Clarke County, Loudoun County, Fairfax County, Fairfax City, Fauquier County, Arlington County, Arlington City, Frederick County, Shenandoah County

Industry/Entity Type

Home Inspection

Number of Pages Required

1 page

Font styles to use
Sans Serif

Requirements
Must have
• My logo
• Company name: Heron Home Inspections, LLC.
• Tom Keller, Jr.
• Owner / Principal Inspector
• 555-418-2973
• tom.heroninspections@mailbox.example
• A space to describe me and my business
Should not have
• Please use the color scheme of the uploads that I provided

```html
<!DOCTYPE html>
<html lang="en">
<head>
<meta charset="utf-8">
<title>Heron Home Inspections, LLC</title>
<link href="https://fonts.googleapis.com/css2?family=Roboto:wght@400;500;700&family=Oswald:wght@400;500&family=Raleway:wght@500&display=swap" rel="stylesheet">
<style>
:root{
  --blue:#3aa5e0;
  --blue-light:#55bff0;
  --navy:#1f3f7a;
  --ink:#333;
  --muted:#555;
  --line:#ddd;
  --dark:#1a1a1a;
  --red:#d9363e;
}
*{box-sizing:border-box;margin:0;padding:0}
html,body{width:688px;height:1200px;overflow:hidden;background:#fff}
body{position:relative;font-family:Roboto,sans-serif;color:var(--ink)}
.abs{position:absolute}
.header-info{font-size:8px;color:#444;display:flex;align-items:center;gap:4px;top:44px;white-space:nowrap}
.header-info svg{width:8px;height:8px;fill:var(--blue)}
.brand{left:0;width:688px;top:18px;text-align:center;color:var(--navy);font-weight:500}
.brand-mark{display:inline-block;width:14px;height:14px;border-radius:50%;background:var(--blue);vertical-align:middle;margin-right:4px}
.brand-name{font-size:20px;letter-spacing:3px;vertical-align:middle}
.brand-sub{font-size:7.5px;letter-spacing:1px;margin-top:2px}
.search-sep{left:620px;top:42px;width:1px;height:14px;background:#999}
.nav{left:50px;top:85px;width:588px;height:38px;display:flex;background:linear-gradient(var(--blue-light),var(--blue));z-index:2}
.nav a{font-size:9px;color:#fff;text-decoration:none;line-height:38px;padding:0 18px}
.nav a.active{background:#3b3b3b;width:70px;text-align:center;padding:0}
.hero{left:0;top:85px;width:688px;height:362px;background:linear-gradient(180deg,#b9c2d6 0%,#8c94a8 45%,#6b5c4e 80%,#5d6a3a 100%)}
.hero-caption{left:56px;top:257px;width:350px;height:82px;background:rgba(255,255,255,.6);padding:14px 17px}
.hero-caption h1{font-family:Oswald,sans-serif;font-weight:500;font-size:23px;color:var(--blue);line-height:1}
.hero-caption p{font-family:Oswald,sans-serif;font-size:12px;color:#333;margin-top:10px}
.hero-arrow{top:350px;width:20px;height:26px;background:rgba(0,0,0,.35);display:flex;align-items:center;justify-content:center}
.hero-arrow svg{width:8px;height:12px;stroke:#fff;fill:none;stroke-width:1.5}
.social-rail{left:669px;top:206px;width:19px}
.social-rail span{display:block;height:19px;margin-bottom:1px}
.welcome{left:50px;top:482px;width:588px;text-align:center}
.welcome h2{font-family:Raleway,sans-serif;font-weight:500;font-size:13px;color:#222}
.welcome h2 em{font-style:normal;color:var(--blue)}
.welcome p{font-size:7.3px;line-height:13.6px;color:var(--muted);margin-top:8px}
.card{top:578px;width:187px}
.card-photo{height:112px;border:2px solid #e4e4e4}
.card h3{font-size:8.8px;font-weight:400;color:var(--blue);margin-top:14px}
.card p{font-size:7px;line-height:11.2px;color:var(--muted);margin-top:8px;text-align:justify;padding-right:10px}
.divider{left:46px;top:783px;width:585px;height:1px;background:var(--line)}
.featured{left:50px;top:809px;width:186px;height:197px;background:#fff;box-shadow:0 0 4px rgba(0,0,0,.3)}
.featured h3{height:33px;background:var(--blue);color:#fff;font-weight:400;font-size:10px;line-height:33px;padding-left:15px}
.featured ul{list-style:none;padding:11px 0 0 15px}
.featured li{font-size:7.2px;color:#444;height:21px;display:flex;align-items:center;gap:6px}
.featured li svg{width:7px;height:7px}
.section-title{font-size:11px;color:#222;font-weight:400}
.post{left:260px;width:180px;height:78px;border-bottom:1px dotted #ccc}
.post-photo{width:63px;height:75px}
.post-body{left:74px;top:0;width:106px}
.post-body h4{font-size:7.6px;font-weight:400;color:var(--navy)}
.post-time{font-size:6.8px;color:#444;margin-top:7px;display:flex;align-items:center;gap:3px}
.post-body p{font-size:6.2px;line-height:12px;color:#555;margin-top:5px}
.quote{left:465px;top:836px;width:170px;height:88px;background:var(--blue);border-radius:3px;padding:10px;color:#fff;font-size:6.4px;line-height:14px}
.quote-tail{left:588px;top:923px;width:0;height:0;border-left:14px solid transparent;border-top:12px solid var(--blue)}
.author-photo{left:477px;top:936px;width:46px;height:46px;border-radius:50%;background:linear-gradient(#c9b7a5,#8a6f5a)}
.author{left:533px;top:941px;font-size:7.5px;color:#444}
.author b{color:var(--red);font-weight:400}
.pager{top:964px;width:12px;height:12px;border:1px solid #ddd;display:flex;align-items:center;justify-content:center}
.pager svg{width:4px;height:6px;stroke:var(--red);fill:none;stroke-width:1.3}
.footer{left:0;top:1030px;width:688px;height:122px;background:linear-gradient(#f4f4f4,#e6e6e6);border-top:3px solid var(--blue)}
.footer-heading{font-size:7.5px;font-weight:400;color:var(--blue)}
.footer-list{font-size:6.5px;color:#333;line-height:17px}
.footer-list div{display:flex;gap:8px;align-items:center;white-space:nowrap}
.footer-list svg{width:7px;height:7px;fill:var(--blue);flex:none}
.partner{top:1077px;height:48px;background:#fff}
.partner span{position:absolute;border-radius:50%}
.follow-circle{top:1108px;width:22px;height:22px;border:1px solid #555;border-radius:50%}
.copyright{left:0;top:1152px;width:688px;height:48px;background:var(--dark);color:#fff;font-size:6.5px;text-align:center;line-height:48px}
</style>
</head>
<body>

<div class="abs header-info" style="left:50px">
  <svg viewBox="0 0 10 10"><rect x="0" y="2" width="10" height="7"/></svg>info@heron.example
</div>
<div class="abs header-info" style="left:152px">
  <svg viewBox="0 0 10 10"><path d="M2 0h2l1 3-1.5 1a6 6 0 0 0 2.5 2.5L7 5l3 1v2c0 1-1 2-2 2C4 10 0 6 0 2c0-1 1-2 2-2z"/></svg>555-418-2973
</div>
<div class="abs brand">
  <div><span class="brand-mark"></span><span class="brand-name">HERON</span></div>
  <div class="brand-sub">HOME INSPECTIONS, LLC</div>
</div>
<div class="abs header-info" style="left:478px">
  <svg viewBox="0 0 10 10"><path d="M5 0a3.5 3.5 0 0 1 3.5 3.5C8.5 6 5 10 5 10S1.5 6 1.5 3.5A3.5 3.5 0 0 1 5 0z"/></svg>P.O. Box 5172 Northern Virginia
</div>
<div class="abs search-sep"></div>
<svg class="abs" style="left:628px;top:45px;width:8px;height:8px" viewBox="0 0 10 10" fill="none" stroke="#555" stroke-width="1.5"><circle cx="4" cy="4" r="3"/><path d="M6.5 6.5 9.5 9.5"/></svg>

<div class="abs hero" role="img" aria-label="Photo of a large two-storey suburban house with a double garage at dusk"></div>
<nav class="abs nav">
  <a class="active" href="#">HOME</a><a href="#">ABOUT</a><a href="#">SERVICES</a><a href="#">INSPECTION</a><a href="#">NEWS</a><a href="#">TESTIMONIALS</a><a href="#">CONTACT</a>
</nav>
<div class="abs hero-caption">
  <h1>HOME INSPECTION</h1>
  <p>Neque porro quisquam est qui dolorem ipsum quia dolor sit amet</p>
</div>
<div class="abs hero-arrow" style="left:50px"><svg viewBox="0 0 8 12"><path d="M7 1 2 6l5 5"/></svg></div>
<div class="abs hero-arrow" style="left:72px"><svg viewBox="0 0 8 12"><path d="M1 1l5 5-5 5"/></svg></div>

<div class="abs social-rail">
  <span style="background:#3b5998"></span><span style="background:#29a9e1"></span><span style="background:#dd4b39"></span><span style="background:#0077b5"></span><span style="background:#cb2027"></span>
</div>

<section class="abs welcome">
  <h2>WELCOME TO <em>HERON INSPECTIONS</em></h2>
  <p>Lorem Ipsum has been the industry's standard dummy text ever since the 1500s, when an unknown printer took a galley of type and scrambled it to make a type specimen book. It has survived not only five centuries, but also the leap into electronic typesetting, remaining essentially unchanged. It was popularised in the 1960s with the release of Letrase aining Lorem Ipsum passages, and more recently with desktop publishing software</p>
</section>

<article class="abs card" style="left:50px">
  <div class="card-photo" role="img" aria-label="House viewed through a magnifying glass" style="background:linear-gradient(#e8ecef,#9aa3a8)"></div>
  <h3>ABOUT US</h3>
  <p>Lorem Ipsum has been the industry's standard dummy text ever since the 1500s, when an unknown printer took a galley of type</p>
</article>
<article class="abs card" style="left:250px">
  <div class="card-photo" role="img" aria-label="House model on top of architectural blueprints" style="background:linear-gradient(#eceae6,#b9ab90)"></div>
  <h3>WHY GET A HOME INSPECTION</h3>
  <p>Lorem Ipsum has been the industry's standard dummy text ever since the 1500s, when an unknown printer took a galley of type</p>
</article>
<article class="abs card" style="left:446px">
  <div class="card-photo" role="img" aria-label="Inspector checking an attic with skylights" style="background:linear-gradient(135deg,#8a6a52,#4e3a2c)"></div>
  <h3>WHY USE HERON INSPECTIONS</h3>
  <p>Lorem Ipsum has been the industry's standard dummy text ever since the 1500s, when an unknown printer took a galley of type</p>
</article>

<div class="abs divider"></div>

<aside class="abs featured">
  <h3>FEATURED WORK SECTION</h3>
  <ul>
    <li><svg viewBox="0 0 8 8" fill="none" stroke="#d9363e"><circle cx="4" cy="4" r="3.3"/><path d="M2.7 2.7l2.6 2.6M5.3 2.7 2.7 5.3"/></svg>Ipsum is simply dummy text</li>
    <li><svg viewBox="0 0 8 8" fill="none" stroke="#d9363e"><circle cx="4" cy="4" r="3.3"/><path d="M2.7 2.7l2.6 2.6M5.3 2.7 2.7 5.3"/></svg>Simply dummy text</li>
    <li><svg viewBox="0 0 8 8" fill="none" stroke="#d9363e"><circle cx="4" cy="4" r="3.3"/><path d="M2.7 2.7l2.6 2.6M5.3 2.7 2.7 5.3"/></svg>Ipsum is simply dummy text</li>
    <li><svg viewBox="0 0 8 8" fill="none" stroke="#d9363e"><circle cx="4" cy="4" r="3.3"/><path d="M2.7 2.7l2.6 2.6M5.3 2.7 2.7 5.3"/></svg>Simply dummy text</li>
    <li><svg viewBox="0 0 8 8" fill="none" stroke="#d9363e"><circle cx="4" cy="4" r="3.3"/><path d="M2.7 2.7l2.6 2.6M5.3 2.7 2.7 5.3"/></svg>Ipsum is simply dummy text</li>
    <li><svg viewBox="0 0 8 8" fill="none" stroke="#d9363e"><circle cx="4" cy="4" r="3.3"/><path d="M2.7 2.7l2.6 2.6M5.3 2.7 2.7 5.3"/></svg>Simply dummy text</li>
    <li><svg viewBox="0 0 8 8" fill="none" stroke="#d9363e"><circle cx="4" cy="4" r="3.3"/><path d="M2.7 2.7l2.6 2.6M5.3 2.7 2.7 5.3"/></svg>Ipsum is simply dummy text</li>
  </ul>
</aside>

<h3 class="abs section-title" style="left:259px;top:811px">Latest Blog</h3>
<div class="abs post" style="top:837px">
  <div class="post-photo" role="img" aria-label="Builder with hard hat holding plans" style="background:linear-gradient(#6fa8d6,#c79a3c)"></div>
  <div class="abs post-body">
    <h4>Nemo Enim Ipsam Volup</h4>
    <div class="post-time"><svg width="6" height="6" viewBox="0 0 8 8" fill="none" stroke="#333"><circle cx="4" cy="4" r="3.3"/><path d="M4 2v2h1.6"/></svg>19.00 pm - 21.00 pm</div>
    <p>Vivamus elementum semper nisi. Lorem ipsum dolor sit amet, sectetuer adipiscing elit.</p>
  </div>
</div>
<div class="abs post" style="top:927px">
  <div class="post-photo" role="img" aria-label="Small house model under a magnifying glass" style="background:linear-gradient(#d9dde0,#7d858a)"></div>
  <div class="abs post-body">
    <h4>Nemo Enim Ipsam Volup</h4>
    <div class="post-time"><svg width="6" height="6" viewBox="0 0 8 8" fill="none" stroke="#333"><circle cx="4" cy="4" r="3.3"/><path d="M4 2v2h1.6"/></svg>19.00 pm - 21.00 pm</div>
    <p>Vivamus elementum semper nisi. Lorem ipsum dolor sit amet, sectetuer adipiscing elit.</p>
  </div>
</div>

<h3 class="abs section-title" style="left:462px;top:808px">Testimonials</h3>
<div class="abs quote"><b style="font-size:11px;line-height:0">&ldquo;</b> Lorem ipsum dolor sit amet, consectetur adipiscing elit, sed do eiusmod tempor incididunt ut labore et dolore magna aliqua. Ut enim ad minim veniam, quis nostrud exercitation Lorem ipsum dolor sit amet,</div>
<div class="abs quote-tail"></div>
<div class="abs author-photo" role="img" aria-label="Portrait of the client giving the testimonial"></div>
<div class="abs author"><b>Sam Porter</b> - &nbsp;Parents Education</div>
<div class="abs pager" style="left:534px"><svg viewBox="0 0 4 6"><path d="M3.5.5 1 3l2.5 2.5"/></svg></div>
<div class="abs pager" style="left:550px"><svg viewBox="0 0 4 6"><path d="M.5.5 3 3 .5 5.5"/></svg></div>

<footer class="abs footer"></footer>
<h5 class="abs footer-heading" style="left:56px;top:1051px">CONTACT US</h5>
<div class="abs footer-list" style="left:56px;top:1064px">
  <div><svg viewBox="0 0 10 10"><path d="M2 0h2l1 3-1.5 1a6 6 0 0 0 2.5 2.5L7 5l3 1v2c0 1-1 2-2 2C4 10 0 6 0 2c0-1 1-2 2-2z"/></svg>555-418-2973 (Phone)</div>
  <div><svg viewBox="0 0 10 10"><rect x="0" y="3" width="10" height="6"/><rect x="2" y="0" width="6" height="3"/></svg>555-418-2974 &nbsp;(Fax)</div>
  <div><svg viewBox="0 0 10 10"><rect x="0" y="2" width="10" height="7"/></svg><span style="text-decoration:underline">tom.heroninspections@mailbox.example</span></div>
  <div style="line-height:9px;margin-top:4px;align-items:flex-start"><svg viewBox="0 0 10 10"><path d="M5 0a3.5 3.5 0 0 1 3.5 3.5C8.5 6 5 10 5 10S1.5 6 1.5 3.5A3.5 3.5 0 0 1 5 0z"/></svg><span>Tom Keller, Jr. &middot; Owner / Principal Inspector<br>P.O. Box 5172 Northern Virginia</span></div>
</div>

<h5 class="abs footer-heading" style="left:212px;top:1052px">PARTNER LOGO</h5>
<div class="abs partner" style="left:212px;width:48px"><span style="left:4px;top:4px;width:40px;height:40px;background:#222"></span></div>
<div class="abs partner" style="left:265px;width:101px"><span style="left:6px;top:6px;width:88px;height:36px;border-radius:18px;background:#2e3f86"></span></div>

<h5 class="abs footer-heading" style="left:435px;top:1051px">LINKS</h5>
<div class="abs footer-list" style="left:435px;top:1064px;line-height:14px">Home<br>About us<br>Services<br>inspection</div>

<h5 class="abs footer-heading" style="left:522px;top:1052px">FOLLOW US</h5>
<p class="abs" style="left:522px;top:1067px;width:120px;font-size:6.3px;line-height:10px;color:#333">Lorem ipsum dolor sit amet, consectetur adipiscing elit. Nulla in purus nibh. Donec ornare felis neque. Nullam tortor!</p>
<div class="abs follow-circle" style="left:523px"></div>
<div class="abs follow-circle" style="left:550px"></div>
<div class="abs follow-circle" style="left:577px"></div>
<div class="abs follow-circle" style="left:605px"></div>

<div class="abs copyright">&copy; 2015 Lumen Web Studio. All Rights Reserved.</div>

</body>
</html>
```